holloway paving service

Needs to have phone number 0418259730 and email markholloway@brightmail.com.au.
ABN 62318470915
name mark holloway

For all your concreting solutions
Excavation
Exposed & colour concrete
House & shed slabs
Driveways
Landing & steps

Contact Information for Business Card

ph 0418259730
email markholloway@brightmail.com.au.
ABN 62318470915
name mark holloway

```html
<!DOCTYPE html>
<html lang="en">
<head>
<meta charset="utf-8">
<title>Holloway Paving Service – Business Card</title>
<link rel="stylesheet" href="https://fonts.googleapis.com/css2?family=Montserrat:wght@600;700&family=Nunito:wght@400;600&display=swap">
<style>
  :root {
    --backdrop: #3b302a;
    --card-white: #f2f2f2;
    --card-white-edge: #e1e1e1;
    --charcoal: #555555;
    --charcoal-dark: #474747;
    --orange: #e8662a;
    --orange-light: #f07a3c;
    --orange-deep: #df5a20;
    --white: #ffffff;
  }
  * { margin: 0; padding: 0; box-sizing: border-box; }
  html, body {
    width: 1200px; height: 960px; overflow: hidden;
    background: var(--backdrop);
  }
  .canvas { position: relative; width: 1200px; height: 960px; }

  .card {
    position: absolute;
    width: 600px; height: 342px;
    overflow: hidden;
    box-shadow: 0 6px 14px rgba(0,0,0,0.35);
  }

  /* Front */
  .card-front {
    left: 302px; top: 127px;
    background: linear-gradient(135deg, var(--card-white) 0%, var(--card-white) 55%, var(--card-white-edge) 100%);
  }
  .front-shapes { position: absolute; inset: 0; }
  .brand-lockup {
    position: absolute; left: 58px; top: 54px;
    display: flex; align-items: center;
  }
  .brand-square {
    width: 62px; height: 62px; background: var(--charcoal);
  }
  .brand-divider {
    width: 2px; height: 96px; background: var(--orange);
    margin: 0 12px 0 40px;
  }
  .brand-text { display: flex; flex-direction: column; }
  .brand-name {
    font-family: "Montserrat", sans-serif; font-weight: 700;
    font-size: 19px; line-height: 1.15; letter-spacing: 0.2px;
    color: var(--orange); text-transform: uppercase;
  }
  .brand-phone {
    font-family: "Nunito", sans-serif; font-weight: 600;
    font-size: 17px; letter-spacing: 1.4px;
    color: var(--orange); margin-top: 4px; padding-left: 62px;
  }
  .contact-block {
    position: absolute; right: 46px; top: 253px;
    text-align: right;
  }
  .contact-name {
    font-family: "Montserrat", sans-serif; font-weight: 700;
    font-size: 22px; color: var(--orange);
    text-transform: uppercase; line-height: 1.1;
  }
  .contact-line {
    font-family: "Nunito", sans-serif; font-weight: 400;
    font-size: 14.5px; color: var(--white);
    line-height: 20px; letter-spacing: 0.3px;
  }
  .contact-name + .contact-line { margin-top: 4px; }

  /* Back */
  .card-back {
    left: 299px; top: 500px;
    background: linear-gradient(100deg, var(--orange-deep) 0%, var(--orange-light) 40%, var(--orange) 70%, var(--orange-deep) 100%);
  }
  .back-brand {
    position: absolute; left: 120px; top: 132px;
    width: 115px; text-align: center;
    font-family: "Montserrat", sans-serif; font-weight: 700;
    font-size: 15px; line-height: 1.25;
    color: var(--white); text-transform: uppercase;
  }
  .service-list {
    position: absolute; left: 254px; top: 125px;
    list-style: none;
  }
  .service-item {
    font-family: "Nunito", sans-serif; font-weight: 400;
    font-size: 14.5px; line-height: 18px; letter-spacing: 0.3px;
    color: var(--white);
    display: flex; align-items: center;
  }
  .service-item::before {
    content: ""; width: 5px; height: 5px; background: var(--white);
    transform: rotate(45deg); margin: 0 8px 0 1px;
  }
</style>
</head>
<body>
<main class="canvas">

  <section class="card card-front" aria-label="Business card front">
    <svg class="front-shapes" width="600" height="342" viewBox="0 0 600 342" aria-hidden="true">
      <polygon points="0,328 288,328 348,227 584,227 584,342 0,342" fill="var(--charcoal)"/>
      <rect x="586" y="227" width="14" height="115" fill="var(--orange)"/>
    </svg>

    <div class="brand-lockup">
      <div class="brand-square" aria-hidden="true"></div>
      <div class="brand-divider" aria-hidden="true"></div>
      <div class="brand-text">
        <span class="brand-name">Holloway Paving<br>Service</span>
        <span class="brand-phone">0418259730</span>
      </div>
    </div>

    <div class="contact-block">
      <p class="contact-name">Mark Holloway</p>
      <p class="contact-line">markholloway@brightmail.com.au</p>
      <p class="contact-line">ABN 62318470915</p>
    </div>
  </section>

  <section class="card card-back" aria-label="Business card back">
    <p class="back-brand">Holloway Paving Service</p>
    <ul class="service-list">
      <li class="service-item">Excavation</li>
      <li class="service-item">Exposed &amp; colour concrete</li>
      <li class="service-item">House &amp; shed slabs</li>
      <li class="service-item">Driveways</li>
      <li class="service-item">Landing &amp; steps</li>
    </ul>
  </section>

</main>
</body>
</html>
```